RWT Fittings Ltd Business Cards

We need a business card with our business logo. We provide window and door installations on high-rises in west coast British Colombia, Canada.

I would like my business information and details on one side of the card, and the other side the company name with logo

Target Market(s)

General Contractors

Industry/Entity Type

Construction

Contact Information for Business Card

one side i want my company name and logo in the dark theme logo that i provided

Requirements
Must have
• Marco Peltieri, 16045518293, RWTFittings@mailbox-demo.com, 1407-5194 Linden Row Burnaby BC, V5H 2K9, Owner & Manager

```html
<!DOCTYPE html>
<html lang="en">
<head>
<meta charset="utf-8">
<title>RWT Fittings Ltd – Business Cards</title>
<link href="https://fonts.googleapis.com/css2?family=Open+Sans:wght@400;600;700&display=swap" rel="stylesheet">
<style>
  :root {
    --backdrop: #3a3a3a;
    --card-white: #ffffff;
    --brand-blue: #29a9e1;
    --brand-grey: #9a9a9a;
    --card-dark: #1b1b1b;
    --text-light: #ffffff;
  }
  * { box-sizing: border-box; margin: 0; padding: 0; }
  html, body { width: 1200px; height: 780px; overflow: hidden; }
  body {
    background: radial-gradient(ellipse at 30% 20%, #5a5a5a 0%, var(--backdrop) 55%, #222 100%);
    font-family: "Open Sans", Arial, sans-serif;
  }
  .sheet {
    position: relative;
    width: 1200px; height: 780px;
    display: flex; align-items: center; justify-content: center; gap: 40px;
  }
  .card {
    position: relative;
    width: 540px; height: 310px;
    overflow: hidden;
    box-shadow: 0 18px 40px rgba(0,0,0,.55);
  }
  /* Front */
  .card--front { background: var(--card-white); }
  .front-shape { position: absolute; inset: 0; }
  .brand {
    position: absolute; top: 58px; right: 40px;
    display: flex; align-items: center; gap: 12px;
  }
  .brand__mark { width: 22px; height: 22px; background: var(--brand-grey); }
  .brand__name {
    font-weight: 700; font-size: 30px; color: var(--brand-blue);
    letter-spacing: .5px;
  }
  .holder {
    position: absolute; left: 34px; top: 150px; color: var(--text-light);
  }
  .holder__name { font-weight: 700; font-size: 17px; letter-spacing: .5px; text-transform: uppercase; }
  .holder__role { font-size: 12px; margin-top: 2px; }
  .holder__address { font-size: 12px; margin-top: 38px; }
  .divider {
    position: absolute; left: 212px; top: 150px;
    width: 1px; height: 62px; background: var(--text-light);
  }
  .contacts {
    position: absolute; left: 230px; top: 150px;
    list-style: none; color: var(--text-light); font-size: 12.5px;
  }
  .contacts li { display: flex; align-items: center; gap: 7px; margin-bottom: 6px; }
  .contacts svg { width: 12px; height: 12px; fill: var(--text-light); }
  /* Back */
  .card--back { background: var(--card-dark); }
  .back-texture {
    position: absolute; inset: 0;
    background: linear-gradient(135deg, #2a2a2a 0%, #161616 60%, #0f0f0f 100%);
  }
  .back-brand {
    position: absolute; inset: 0;
    display: flex; align-items: center; justify-content: center; gap: 10px;
  }
  .back-brand .brand__mark { width: 16px; height: 16px; }
  .back-brand .brand__name { font-size: 22px; }
</style>
</head>
<body>
<main class="sheet">
  <section class="card card--front" aria-label="Business card front">
    <svg class="front-shape" viewBox="0 0 540 310" preserveAspectRatio="none" aria-hidden="true">
      <path d="M0 110 L0 310 L540 310 L540 215 C400 195 250 140 130 0 L0 0 Z" fill="#29a9e1"/>
      <path d="M140 12 C250 130 390 188 520 212" fill="none" stroke="#9a9a9a" stroke-width="2.5"/>
    </svg>
    <div class="brand">
      <span class="brand__mark"></span>
      <span class="brand__name">RWT Fittings Ltd</span>
    </div>
    <div class="holder">
      <p class="holder__name">Owen Hartley</p>
      <p class="holder__role">Managing Director</p>
      <p class="holder__address">Your address, City State, Zip 1234</p>
    </div>
    <span class="divider"></span>
    <ul class="contacts">
      <li><svg viewBox="0 0 24 24"><path d="M6.6 10.8a15 15 0 0 0 6.6 6.6l2.2-2.2c.3-.3.7-.4 1-.2 1.1.4 2.3.6 3.6.6.6 0 1 .4 1 1V20c0 .6-.4 1-1 1A17 17 0 0 1 3 4c0-.6.4-1 1-1h3.5c.6 0 1 .4 1 1 0 1.3.2 2.5.6 3.6.1.3 0 .7-.2 1z"/></svg>123 456 789</li>
      <li><svg viewBox="0 0 24 24"><path d="M2 5h20v14H2z M4 7l8 6 8-6v-.1H4z" fill-rule="evenodd"/></svg>info@yourmail-demo.com</li>
      <li><svg viewBox="0 0 24 24"><circle cx="12" cy="12" r="10"/></svg>www.yoursite-demo.com</li>
    </ul>
  </section>

  <section class="card card--back" aria-label="Business card back">
    <div class="back-texture" role="img" aria-label="Dark tonal repeating building pattern background"></div>
    <div class="back-brand">
      <span class="brand__mark"></span>
      <span class="brand__name">RWT Fittings Ltd</span>
    </div>
  </section>
</main>
</body>
</html>
```